Trade Show booth design

I need the following designs for my trade booth:
1. backboard design 3m Wx2mH
2. Tressle table, tablecloth front panel design 1800W x 740mmH
3. Pop-up banner. I have included our logos and some design content ideas:
Headline:
"Cleaner Classrooms. Safer Schools."
Subheadline:
"Specialist Cleaning Solutions for Education Facilities"
Key Points to Grab Attention:
Healthy Environments: Create hygienic, safe learning spaces for students and staff with our expert cleaning services.
Tailored to Your Needs: Custom cleaning plans for classrooms, labs, libraries, and sports facilities.
Affordable Excellence: Premium results without premium costs – tailored plans mean you only pay for what you need.
Safety First: All staff are trained, highly vetted, and hold current Working with Children Checks (WWCC).
Eco-Conscious Cleaning: Using non-toxic, eco-friendly products certified for health and safety.
What Schools Really Need:
Reliability: Consistent, high-quality cleaning from a trusted provider.
Cost-Effectiveness: Solutions that fit tight budgets while maintaining high standards.
Expertise: Over 30 years of experience in education facility cleaning.
Disinfection Services: Focus on high-touch areas to reduce the spread of germs and ensure peace of mind.
Visual Elements:
Images of bright, clean classrooms, a happy teacher welcoming students, or students collaborating in a spotless library.
Icons representing safety (shield), hygiene (sparkling star), and eco-friendliness (leaf).
Your logo with the tagline: "Trusted by Queensland Schools Since 1995."
Call-to-Action:
"Visit us to discuss your school’s cleaning needs and book a FREE consultation."
Include contact details: Phone: 1300 594 316 | Website: www.brightmorefacility.com.au
Target Market(s)
Education sector
Industry/Entity Type
Commercial Cleaning
Font styles to use
Other font styles liked:
- Montserrat
Look and feel

```html
<!DOCTYPE html>
<html lang="en">
<head>
<meta charset="utf-8">
<title>Brightmore Facility Services – Trade Show Booth</title>
<link href="https://fonts.googleapis.com/css2?family=Bebas+Neue&family=Poppins:wght@400;500;600;700;800&display=swap" rel="stylesheet">
<style>
  :root{
    --navy:#1d3b62;
    --navy-deep:#162f50;
    --cyan:#14a9e2;
    --cyan-light:#4cc4ef;
    --white:#ffffff;
    --ink:#1d3050;
    --stage:#f3f4f7;
  }
  *{margin:0;padding:0;box-sizing:border-box}
  html,body{width:1200px;height:854px;overflow:hidden;background:var(--stage)}
  body{position:relative;font-family:"Poppins",sans-serif;color:var(--ink)}

  /* ---------- Backboard ---------- */
  .backboard{position:absolute;left:40px;top:150px;width:720px;height:540px;background:var(--white);overflow:hidden}
  .backboard-shapes{position:absolute;inset:0}
  .brand{position:absolute;display:flex;align-items:center;gap:12px}
  .brand-mark{width:18px;height:18px;border-radius:50%;background:var(--navy)}
  .brand-name{font-family:"Poppins",sans-serif;font-weight:600;color:var(--navy);line-height:1.15}
  .backboard .brand{left:40px;top:52px}
  .backboard .brand-name{font-size:26px}
  .headline-top{position:absolute;left:40px;top:146px;font-family:"Bebas Neue",sans-serif;font-size:47px;color:var(--cyan);letter-spacing:.5px;line-height:1}
  .headline-bottom{position:absolute;left:40px;top:192px;font-family:"Poppins",sans-serif;font-weight:800;font-size:35px;color:var(--navy);line-height:1}
  .sub-band{position:absolute;left:40px;top:249px;width:432px;height:98px;padding:14px 0 0 16px;color:var(--white)}
  .sub-band .line-1{font-family:"Bebas Neue",sans-serif;font-size:36px;line-height:1;letter-spacing:.3px;padding-bottom:6px;border-bottom:1px solid rgba(255,255,255,.45);width:308px}
  .sub-band .line-2{font-weight:700;font-size:21px;margin-top:6px;letter-spacing:.3px}
  .benefits{position:absolute;left:40px;top:376px;list-style:none}
  .benefits li{display:flex;align-items:flex-start;gap:14px;font-size:14.5px;line-height:1.1;margin-bottom:11px;width:210px}
  .benefits svg{flex:none;width:18px;height:18px}
  .needs{position:absolute;left:272px;top:376px}
  .needs h3{font-weight:800;font-size:17px;color:var(--cyan);line-height:1.1;margin-bottom:10px}
  .needs ul{list-style:none}
  .needs li{display:flex;align-items:center;gap:8px;font-size:14.5px;margin-bottom:6px}
  .needs li::before{content:"";width:16px;height:2px;background:var(--cyan);box-shadow:-2px 0 0 2px var(--cyan) inset;border-left:5px solid var(--cyan);border-radius:2px}
  .cta{position:absolute;left:472px;top:350px;width:248px;text-align:center;color:var(--white)}
  .cta-free{font-family:"Poppins",sans-serif;font-weight:800;font-size:82px;line-height:.9;letter-spacing:1px}
  .cta-label{font-weight:700;font-size:23px;line-height:1.2;margin-top:4px;letter-spacing:.5px}
  .phone-pill{margin:8px auto 0;width:200px;height:36px;border-radius:18px;background:var(--white);display:flex;align-items:center;justify-content:center;gap:8px;color:var(--navy);font-weight:700;font-size:24px}
  .phone-pill svg{width:22px;height:22px}
  .cta-web{font-weight:700;font-size:11.5px;margin-top:10px}

  /* ---------- Pop-up banner ---------- */
  .popup{position:absolute;left:810px;top:120px;width:320px;height:610px;background:var(--white);overflow:hidden}
  .popup-shapes{position:absolute;inset:0}
  .popup .brand{left:0;right:0;top:24px;justify-content:center}
  .popup .brand-name{font-size:16px}
  .popup-headline{position:absolute;left:0;right:0;top:318px;text-align:center;font-family:"Bebas Neue",sans-serif;font-size:35px;line-height:1}
  .popup-headline .navy{color:var(--navy)}
  .popup-headline .cyan{color:var(--cyan)}
  .popup-band{position:absolute;left:0;top:396px;width:320px;height:64px;background:var(--navy);color:var(--white);text-align:center;padding-top:10px}
  .popup-band .line-1{font-family:"Bebas Neue",sans-serif;font-size:21px;line-height:1}
  .popup-band .line-2{font-weight:700;font-size:16.5px;line-height:1.4}
  .credentials{position:absolute;left:32px;top:478px;list-style:none;width:270px}
  .credentials li{display:flex;align-items:flex-start;gap:12px;font-size:9.2px;font-weight:500;text-transform:uppercase;line-height:1.4;margin-bottom:12px}
  .credentials svg{flex:none;width:24px;height:24px}
  .popup-footer{position:absolute;left:0;bottom:0;width:320px;height:30px;background:var(--cyan);color:var(--white);display:flex;align-items:center;justify-content:center;gap:6px;font-size:10.5px;font-weight:500;letter-spacing:.8px}
  .popup-footer svg{width:11px;height:11px}
</style>
</head>
<body>

<section class="backboard" aria-label="Backboard">
  <svg class="backboard-shapes" viewBox="0 0 720 540" width="720" height="540">
    <rect x="472" y="305" width="248" height="235" fill="var(--cyan)"/>
    <rect x="40" y="249" width="440" height="98" rx="14" fill="var(--navy)"/>
    <circle cx="560" cy="158" r="200" fill="#dff3fb"/>
    <circle cx="560" cy="158" r="194" fill="var(--navy)"/>
    <circle cx="564" cy="158" r="174" fill="var(--white)"/>
    <circle cx="566" cy="156" r="166" fill="url(#classroomTone)" role="img" aria-label="Photo of a bright, empty classroom with wooden desks and chairs"/>
    <defs>
      <linearGradient id="classroomTone" x1="0" y1="0" x2="1" y2="1">
        <stop offset="0" stop-color="#f3d996"/>
        <stop offset=".5" stop-color="#d9b57e"/>
        <stop offset="1" stop-color="#b98b52"/>
      </linearGradient>
    </defs>
  </svg>

  <div class="brand"><span class="brand-mark"></span><span class="brand-name">Brightmore<br>Facility Services</span></div>

  <h1 class="headline-top">Cleaner Classrooms</h1>
  <h2 class="headline-bottom">SAFER SCHOOLS</h2>

  <div class="sub-band">
    <div class="line-1">Specialist Cleaning Solutions</div>
    <div class="line-2">FOR EDUCATION FACILITIES</div>
  </div>

  <ul class="benefits">
    <li><svg viewBox="0 0 20 20"><path d="M2 10 10 3l8 7v8H2z" fill="none" stroke="var(--cyan)" stroke-width="2.4" stroke-linejoin="round"/></svg>Healthy Environments</li>
    <li><svg viewBox="0 0 20 20"><path d="M10 2v8m-4-3 4 4 4-4M2 13h5l3 3h8v2H2z" fill="none" stroke="var(--cyan)" stroke-width="2.2"/></svg>Tailored to Your Needs</li>
    <li><svg viewBox="0 0 20 20"><circle cx="10" cy="10" r="8" fill="none" stroke="var(--cyan)" stroke-width="2.2"/><path d="M6 10l3 3 5-6" fill="none" stroke="var(--cyan)" stroke-width="2.2"/></svg>Affordable Excellence to Your Needs</li>
    <li><svg viewBox="0 0 20 20"><path d="M10 1 17 4v6c0 5-3.5 8-7 9-3.5-1-7-4-7-9V4z" fill="var(--cyan)"/><path d="M6.5 10l2.5 2.5 4.5-5" fill="none" stroke="#fff" stroke-width="2"/></svg>Safety First</li>
    <li><svg viewBox="0 0 20 20"><path d="M10 1C7 6 4 9 4 13a6 6 0 0 0 12 0c0-4-3-7-6-12z" fill="var(--cyan)"/></svg>Eco-Conscious Cleaning</li>
  </ul>

  <div class="needs">
    <h3>What Schools<br>Really Need:</h3>
    <ul>
      <li>Reliability</li>
      <li>Cost-Effectiveness</li>
      <li>Expertise</li>
      <li>Disinfection Services</li>
    </ul>
  </div>

  <div class="cta">
    <div class="cta-free">FREE</div>
    <div class="cta-label">CONSULTATION</div>
    <div class="phone-pill">
      <svg viewBox="0 0 24 24"><circle cx="12" cy="12" r="12" fill="var(--navy)"/><path d="M8.5 6.5c.5-.5 1.2-.4 1.5.1l1.2 2c.3.5.2 1-.2 1.4l-.8.7c.6 1.3 1.6 2.4 3 3.1l.7-.8c.4-.4 1-.5 1.4-.2l2 1.2c.5.3.6 1 .1 1.5l-1 1c-.8.8-2.1.9-3.1.3a14 14 0 0 1-5.8-5.8c-.6-1-.5-2.3.3-3.1z" fill="#fff"/></svg>
      1300 594 316
    </div>
    <div class="cta-web">www.brightmorefacility.com.au</div>
  </div>
</section>

<section class="popup" aria-label="Pop-up banner">
  <svg class="popup-shapes" viewBox="0 0 320 610" width="320" height="610">
    <path d="M0 0h40L18 22 0 0z" fill="var(--cyan)"/>
    <circle cx="164" cy="128" r="176" fill="var(--cyan)"/>
    <circle cx="150" cy="104" r="164" fill="var(--white)"/>
    <path d="M0 96h320v30a164 164 0 0 1-320 0z" fill="url(#popupTone)" role="img" aria-label="Photo of a bright classroom with green chalkboards and rows of wooden desks"/>
    <defs>
      <linearGradient id="popupTone" x1="0" y1="0" x2="0" y2="1">
        <stop offset="0" stop-color="#f2f3f3"/>
        <stop offset=".45" stop-color="#e6e4dc"/>
        <stop offset="1" stop-color="#c08c54"/>
      </linearGradient>
    </defs>
  </svg>

  <div class="brand"><span class="brand-mark"></span><span class="brand-name">Brightmore<br>Facility Services</span></div>

  <h2 class="popup-headline"><span class="navy">Creating Cleaner, Safer</span><br><span class="cyan">Learning Environments</span></h2>

  <div class="popup-band">
    <div class="line-1">Specialists in Education Facility Cleaning</div>
    <div class="line-2">&amp; ECO FRIENDLY SERVICES</div>
  </div>

  <ul class="credentials">
    <li><svg viewBox="0 0 24 24"><circle cx="12" cy="12" r="11" fill="none" stroke="var(--cyan)" stroke-width="2"/><circle cx="12" cy="12" r="7.5" fill="var(--cyan)"/><path d="M8.5 12l2.5 2.5 4.5-5" fill="none" stroke="#fff" stroke-width="2"/></svg>Over 30 years of expertise in commercial cleaning</li>
    <li><svg viewBox="0 0 24 24"><circle cx="12" cy="12" r="11" fill="var(--cyan)"/><path d="M5 13l4-3 3 2 3-2 4 3-4 3-3-2-3 2z" fill="#fff"/></svg>Trusted by schools, universities, and TAFEs across Queensland</li>
    <li><svg viewBox="0 0 24 24"><circle cx="12" cy="12" r="11" fill="none" stroke="var(--cyan)" stroke-width="2"/><path d="M12 5c-3 3-4 6-2 9 1 1 3 1 4 0 2-3 1-6-2-9z" fill="var(--cyan)"/></svg>100% carbon neutral and eco-certified services.</li>
  </ul>

  <div class="popup-footer">
    <svg viewBox="0 0 12 12"><circle cx="6" cy="6" r="5" fill="none" stroke="#fff" stroke-width="1.2"/><path d="M1 6h10M6 1c-2 3-2 7 0 10M6 1c2 3 2 7 0 10" fill="none" stroke="#fff" stroke-width="1"/></svg>
    www.brightmorefacility.com.au
  </div>
</section>

</body>
</html>
```